Business Card for premium dental clinic

We are a premium dental clinic based in Brasov, Romania with more than 15 year on the market, providing quality dental treatment made by a team of more specialized dentists, working with modern equipment as a solution to beautiful and healthy teeth.

Our current logo for the clinic use 2 square with colors black and gold - dr Ternisu - studio, using family fonts Bodoni, Myriad Pro and Segoe Print.
Depending on the printing we used some gold CMYK background or gold foil picture background or a gold gradient.
We want a business card:
- eye catching business card
- distinguished business card
- premium design
- to keep the color scheme of black and gold
- to attract the customers to spent time reading the information
- modern concept

```html
<!DOCTYPE html>
<html lang="en">
<head>
<meta charset="utf-8">
<title>Lumen Dental Clinic – Business Card</title>
<link rel="stylesheet" href="https://fonts.googleapis.com/css2?family=Oswald:wght@300;400&family=Roboto:wght@400;500&display=swap">
<style>
  :root {
    --backdrop: #3a3a3c;
    --card-dark: #2b2b2d;
    --gold-light: #f7d24a;
    --gold-mid: #e0b020;
    --gold-deep: #b88a12;
    --white: #ffffff;
    --ink: #1d1d1f;
    --text-light: #f2f2f2;
  }
  * { box-sizing: border-box; margin: 0; padding: 0; }
  html, body { width: 799px; height: 1200px; overflow: hidden; }
  body {
    background: var(--backdrop);
    display: flex;
    flex-direction: column;
    align-items: center;
    justify-content: center;
    gap: 150px;
  }
  .card {
    position: relative;
    width: 680px;
    height: 390px;
    background: var(--card-dark);
    overflow: hidden;
    box-shadow: 0 14px 30px rgba(0,0,0,0.45);
  }
  .gold-foil {
    position: absolute;
    left: 0; top: 0; bottom: 0;
    width: 306px;
    background:
      radial-gradient(circle at 30% 25%, var(--gold-light) 0%, transparent 55%),
      radial-gradient(circle at 70% 80%, var(--gold-light) 0%, transparent 50%),
      linear-gradient(135deg, var(--gold-mid), var(--gold-light) 45%, var(--gold-deep) 100%);
  }
  .name-plate {
    position: absolute;
    background: var(--white);
    color: var(--ink);
    font-family: "Oswald", sans-serif;
    font-weight: 300;
    display: flex;
    align-items: baseline;
    justify-content: center;
    white-space: nowrap;
  }
  .name-plate .title { font-size: 0.5em; margin-right: 4px; }
  .card--front .name-plate {
    left: 58px; top: 112px;
    width: 248px; height: 100px;
    font-size: 60px;
    line-height: 100px;
  }
  .card--back .name-plate {
    left: 166px; top: 40px;
    width: 140px; height: 60px;
    font-size: 36px;
    line-height: 60px;
  }
  .clinic-name {
    position: absolute;
    font-family: "Roboto", sans-serif;
    font-weight: 500;
    color: var(--text-light);
    line-height: 1.1;
  }
  .card--front .clinic-name {
    left: 360px; top: 140px;
    font-size: 40px;
  }
  .card--back .clinic-name {
    left: 380px; top: 56px;
    font-size: 30px;
    text-align: right;
  }
  .clinic-name .sub { display: block; }
  .contacts {
    position: absolute;
    left: 336px; top: 180px;
    list-style: none;
    font-family: "Roboto", sans-serif;
    font-weight: 400;
    font-size: 17px;
    color: var(--text-light);
  }
  .contacts li { display: flex; align-items: center; gap: 10px; margin-bottom: 6px; }
  .contacts .icon { width: 14px; height: 14px; flex: none; }
  .contacts .address { padding-left: 0; margin-top: 4px; line-height: 1.3; }
</style>
</head>
<body>

  <section class="card card--front" aria-label="Business card front">
    <div class="gold-foil" role="img" aria-label="Crumpled gold foil texture"></div>
    <div class="name-plate"><span class="title">dr.</span>ternisu</div>
    <div class="clinic-name">lumen<span class="sub">dental clinic</span></div>
  </section>

  <section class="card card--back" aria-label="Business card back">
    <div class="gold-foil" role="img" aria-label="Crumpled gold foil texture"></div>
    <div class="name-plate"><span class="title">dr.</span>ternisu</div>
    <div class="clinic-name">lumen<span class="sub">dental clinic</span></div>
    <ul class="contacts">
      <li>
        <svg class="icon" viewBox="0 0 16 16" aria-hidden="true"><path fill="#e0b020" d="M3.5 1l2.5 3-1.5 2c1 2 3 4 5 5l2-1.5 3 2.5-1.5 2.5C8 15 1 8 1 2.5z"/></svg>
        268-410-7725
      </li>
      <li>
        <svg class="icon" viewBox="0 0 16 16" aria-hidden="true"><rect x="1" y="3" width="14" height="10" fill="#e0b020"/><path d="M1 3l7 6 7-6" fill="none" stroke="#2b2b2d" stroke-width="1.4"/></svg>
        hello@lumenclinic.ro
      </li>
      <li>
        <svg class="icon" viewBox="0 0 16 16" aria-hidden="true"><circle cx="8" cy="8" r="7" fill="#e0b020"/><path d="M1 8h14M8 1c-3 3-3 11 0 14M8 1c3 3 3 11 0 14" fill="none" stroke="#2b2b2d" stroke-width="1"/></svg>
        www.lumenclinic.ro
      </li>
      <li class="address">18 Strada Brazilor, Old Town,<br>Brasov, RO 500123</li>
    </ul>
  </section>

</body>
</html>
```